Call Center In Need of Website Design

We are a call center that provides inbound and outbound calling & marketing services for eCommerce store. We would like to see a fun, creative, playful design that is simple.

Here are some sample design sites we like;
- https://www.velmoreline.com/
- https://pindrask.io/
- https://www.glimbertic.com/live-chat-software/
- https://www.zavrolin.com/

Here are some competitor sites;
- https://www.ostrevaglinks.com/
- https://www.helpkestrel.com/

I have attached website content for your use.

Target Market(s)

eCommerce

Coding

Coded - Design and coding required

Number of Pages Required

5+ page

Font styles to use
Sans Serif

Colors

Designer to choose colors to be used in the design.

Requirements
Must have
• Must have designs for the following 5 separate pages;
• 1. Home (landing)
• - This will be were the design style really needs to show.
• - Just needs to touch on key services
• - CTA
• 2. About Us
• - Basic page for about me paragraph
• 3. Services
• - List of services with icons
• - Click on service type to expand details or hover over service icon to view popup bubble with details about that service
• 4. Pricing
• - Option to bundle 1(one) digital service plan and 1(one) call center service plan
• - Bundling adds 10% monthly discount to over all price
• - Customer does NOT have to bundle
• - FAQ
• 5. Contact Us
• - Include a capture form (name, company name, email, phone, message)
• - Contact info
• - Business hours
• When customer purchases their desired plan, then they are taken to a page where they must schedule a call with an account rep.
Nice to have
• home page animations
Should not have
• All information on Home/Landing page.

```html
<!DOCTYPE html>
<html lang="en">
<head>
<meta charset="utf-8">
<title>Orbitale — Omnichannel Customer Care</title>
<link href="https://fonts.googleapis.com/css2?family=Montserrat:wght@500;600;700&family=Nunito+Sans:wght@300;400;600;700&display=swap" rel="stylesheet">
<style>
:root{
  --navy:#383787;
  --navy-deep:#2d2b7c;
  --navy-soft:#4a4a9c;
  --teal:#6cc5ac;
  --teal-light:#7fd9c1;
  --mist:#eef6f8;
  --white:#ffffff;
  --ink:#333344;
  --muted:#8a8a99;
  --grey:#9a9a9a;
  --coral:#ee6a68;
  --social-1:#2aa3e0;
  --social-2:#3b5a9a;
  --social-3:#4a7aa6;
  --social-4:#dd4b39;
}
*{box-sizing:border-box;margin:0;padding:0}
html,body{width:794px;height:1200px;overflow:hidden}
body{position:relative;font-family:"Nunito Sans",sans-serif;color:var(--ink);background:var(--white)}
.abs{position:absolute}
.heading{font-family:"Montserrat",sans-serif;font-weight:700}

/* hero */
.hero{position:absolute;left:0;top:0;width:794px;height:370px;background:var(--navy)}
.hero-texture{position:absolute;inset:0;background:radial-gradient(ellipse 60% 70% at 20% 80%,#3f3e92 0%,rgba(56,55,135,0) 70%),radial-gradient(ellipse 50% 60% at 85% 20%,#403f94 0%,rgba(56,55,135,0) 70%)}
.brand{position:absolute;left:107px;top:22px;display:flex;align-items:center;gap:12px}
.brand-dot{width:36px;height:36px;border:3px solid var(--teal);border-radius:50%}
.brand-name{font-family:"Montserrat",sans-serif;font-weight:500;font-size:25px;letter-spacing:5px;color:var(--white)}
.nav{position:absolute;top:40px;left:374px;display:flex;gap:21px;font-size:7px;font-weight:600;letter-spacing:.5px;text-transform:uppercase;color:#c7c8ea}
.nav .active{color:var(--white);font-weight:700}
.hero-title{position:absolute;left:106px;top:140px;font-size:23px;line-height:27px;color:var(--white)}
.hero-sub{position:absolute;left:106px;top:205px;font-size:12px;color:var(--white)}
.hero-links{position:absolute;left:106px;top:247px;display:flex;gap:15px;font-size:7px;font-weight:700;color:var(--white);text-transform:uppercase}
.hero-links span{border-bottom:2px solid var(--teal);padding-bottom:2px}
.hero-art{position:absolute;left:432px;top:88px;width:256px;height:216px;border-radius:50% 50% 14px 14px / 38% 38% 14px 14px;background:radial-gradient(ellipse 45% 40% at 45% 58%,var(--coral) 0%,#c45a7a 40%,#6464b4 75%,var(--navy-soft) 100%)}

/* what we do */
.services{position:absolute;left:0;top:370px;width:794px;height:212px;background:var(--teal)}
.service-card{position:absolute;top:40px;width:124px;height:133px;background:var(--white);border-radius:3px;overflow:hidden;box-shadow:0 2px 4px rgba(0,0,0,.12)}
.service-icon{height:75px;background:var(--navy);display:flex;align-items:center;justify-content:center}
.service-name{margin:12px 0 0 10px;font-size:8px;font-weight:700;color:#222}
.service-name::before{content:"•";margin-right:5px}
.service-items{margin:6px 0 0 10px;font-size:6.5px;line-height:10px;color:var(--muted)}
.about-title{position:absolute;left:397px;top:41px;font-size:12px;color:var(--white)}
.rule{position:absolute;width:22px;height:1px;background:var(--white)}
.about-text{position:absolute;left:397px;top:80px;width:295px;font-size:6.9px;line-height:13px;color:var(--white)}
.btn-outline{position:absolute;border:1px solid var(--white);border-radius:3px;color:var(--white);font-size:7.5px;font-weight:700;display:flex;align-items:center;justify-content:center}

/* faq */
.faq{position:absolute;left:0;top:582px;width:794px;height:328px;background:var(--mist)}
.faq-title{position:absolute;left:0;width:794px;top:40px;text-align:center;font-size:20px;color:var(--navy-deep)}
.faq-rule{position:absolute;left:386px;top:69px;width:22px;height:1px;background:var(--navy-deep)}
.faq-sub{position:absolute;left:0;width:794px;top:87px;text-align:center;font-size:8px;color:#333}
.faq-card{position:absolute;left:149px;top:123px;width:496px;height:125px;background:var(--white);box-shadow:0 2px 6px rgba(0,0,0,.12)}
.faq-quote{position:absolute;left:4px;top:0;font-family:"Montserrat",sans-serif;font-weight:700;font-size:90px;line-height:80px;color:#f1f2f4}
.faq-answer{position:absolute;left:80px;top:25px;width:375px;font-size:7.6px;line-height:13px;color:#444}
.faq-question{position:absolute;left:80px;top:87px;font-size:7.8px;font-weight:600;color:#333}
.faq-brand{position:absolute;left:287px;top:65px;display:flex;align-items:center;gap:10px}
.faq-brand .brand-dot{width:32px;height:32px;border-width:2px}
.faq-brand .brand-name{color:#333;font-size:19px;letter-spacing:4px}
.dots{position:absolute;left:374px;top:270px;display:flex;gap:5px}
.dots i{width:4px;height:4px;border-radius:50%;background:#222}
.dots i.on{width:5px;height:5px;margin-top:-.5px;background:var(--teal)}

/* callback */
.callback{position:absolute;left:0;top:910px;width:794px;height:223px;background:var(--teal)}
.callback-texture{position:absolute;inset:0;background:radial-gradient(ellipse 40% 60% at 10% 50%,#74cbb3 0%,rgba(108,197,172,0) 70%),radial-gradient(ellipse 40% 60% at 92% 50%,#74cbb3 0%,rgba(108,197,172,0) 70%)}
.contact-panel{position:absolute;left:124px;top:34px;width:182px;height:154px;background:var(--teal-light)}
.contact-title{position:absolute;left:15px;top:18px;font-size:10px;color:var(--white)}
.contact-row{position:absolute;left:15px;display:flex;gap:7px;font-size:7.2px;line-height:12.5px;color:var(--white)}
.contact-row svg{flex:none;margin-top:2px}
.callback-title{position:absolute;left:323px;top:33px;font-size:19px;color:var(--white)}
.field{position:absolute;width:168px;height:25px;background:var(--teal-light);border:1px solid #9ae5d0;font-size:7px;color:var(--white);padding:8px 10px}
.field.strong{font-weight:700}

/* footer */
.footer{position:absolute;left:0;top:1133px;width:794px;height:67px;background:var(--white)}
.copyright{position:absolute;left:106px;top:20px;font-size:7px;line-height:14px;color:var(--grey)}
.foot-nav{position:absolute;left:272px;top:28px;display:flex;gap:20px;font-size:8px;color:#555}
.foot-nav .active{color:var(--teal)}
.social{position:absolute;left:608px;top:24px;display:flex;gap:3px}
.social i{width:17px;height:17px;border-radius:2px}
</style>
</head>
<body>

<header class="hero">
  <div class="hero-texture" role="img" aria-label="Faint doodle pattern of communication icons"></div>
  <div class="brand"><span class="brand-dot"></span><span class="brand-name">ORBITALE</span></div>
  <nav class="nav">
    <span class="active">Home</span><span>About Us</span><span>Services</span><span>Pricing</span><span>Contact Us</span><span>Account</span>
  </nav>
  <h1 class="hero-title heading">Orbitale Is An<br>Omnichannel</h1>
  <p class="hero-sub">Provider For Customer Care</p>
  <div class="hero-links"><span>Learn More</span><span>Get Started</span></div>
  <div class="hero-art" role="img" aria-label="Illustration of a laptop, tablet and phone surrounded by chat bubbles, media and shopping icons"></div>
</header>

<section class="services">
  <div class="service-card" style="left:114px">
    <div class="service-icon">
      <svg width="56" height="44" viewBox="0 0 56 44" aria-hidden="true">
        <rect x="8" y="8" width="40" height="26" rx="1.5" fill="none" stroke="#fff" stroke-width="2"/>
        <path d="M3 36h50v3H3z" fill="#fff"/>
        <circle cx="22" cy="12" r="7" fill="var(--navy)" stroke="#fff" stroke-width="2"/>
        <circle cx="22" cy="12" r="2.5" fill="none" stroke="#fff" stroke-width="1.5"/>
        <path d="M26 16l12 12" stroke="#fff" stroke-width="2.5" stroke-linecap="round"/>
        <circle cx="39" cy="29" r="2.5" fill="none" stroke="#fff" stroke-width="1.5"/>
      </svg>
    </div>
    <p class="service-name">Digital Services</p>
    <p class="service-items">Email Support<br>Live Chat Support</p>
  </div>
  <div class="service-card" style="left:249px">
    <div class="service-icon">
      <svg width="50" height="48" viewBox="0 0 50 48" aria-hidden="true">
        <path d="M12 22a13 13 0 0 1 26 0" fill="none" stroke="#fff" stroke-width="2.5"/>
        <rect x="8" y="19" width="6" height="10" rx="2" fill="#fff"/>
        <rect x="36" y="19" width="6" height="10" rx="2" fill="#fff"/>
        <path d="M39 29c0 6-5 9-11 9" fill="none" stroke="#fff" stroke-width="2"/>
        <circle cx="27" cy="38" r="2.5" fill="#fff"/>
      </svg>
    </div>
    <p class="service-name">Call Center Services</p>
    <p class="service-items">Answering service<br>Welcome Calls</p>
  </div>
  <h2 class="about-title heading">What We Do</h2>
  <span class="rule" style="left:397px;top:63px"></span>
  <p class="about-text">Orbitale is your personal customer service and product research team. We love eCommerce, but we love seeing business owners succeed even more! That is exactly why we have developed the processes and technology to take care of the most over looked areas in eCommerce - Customer Service and Retention.</p>
  <div class="btn-outline" style="left:397px;top:148px;width:49px;height:25px">More</div>
</section>

<section class="faq">
  <h2 class="faq-title heading">Frequently Asked Queтions</h2>
  <span class="faq-rule"></span>
  <p class="faq-sub">Lorem Ipsum Dolor Sit Amet Consectetor Lorem Ipsum Dolor Sit Amet Consectetor</p>
  <article class="faq-card">
    <span class="faq-quote" aria-hidden="true">“</span>
    <p class="faq-answer">The free trial only relates to the "call center" service packages! There is no hidden fine print or fees to get started. We don't even require any payment info, signatures, or deposits. If you don't like us or our service, just simply walk away.</p>
    <p class="faq-question">Is the free trial really free?</p>
    <div class="faq-brand"><span class="brand-dot"></span><span class="brand-name">ORBITALE</span></div>
  </article>
  <svg class="abs" style="left:153px;top:266px" width="16" height="8" viewBox="0 0 16 8"><path d="M15 4H2M5 1L1.5 4 5 7" stroke="#888" stroke-width="1.5" fill="none"/></svg>
  <svg class="abs" style="left:625px;top:266px" width="16" height="8" viewBox="0 0 16 8"><path d="M1 4h13M11 1l3.5 3L11 7" stroke="#888" stroke-width="1.5" fill="none"/></svg>
  <div class="dots"><i class="on"></i><i></i><i></i><i></i><i></i></div>
</section>

<section class="callback">
  <div class="callback-texture" role="img" aria-label="Faint doodle pattern of business and communication icons"></div>
  <div class="contact-panel">
    <h3 class="contact-title heading">Contact Details</h3>
    <span class="rule" style="left:15px;top:37px"></span>
    <div class="contact-row" style="top:60px">
      <svg width="8" height="8" viewBox="0 0 10 10"><path d="M2 1l2 2-1 1.5c.8 1.5 1.7 2.4 3 3L7.5 6l2 2-1.5 1.5C4.5 9 1 5.5.5 2.5z" fill="#fff"/></svg>
      <span>Phone: (800) 555-0139</span>
    </div>
    <div class="contact-row" style="top:79px">
      <svg width="8" height="7" viewBox="0 0 10 8"><rect x=".5" y=".5" width="9" height="7" fill="none" stroke="#fff"/><path d="M.5 .5L5 4.5 9.5.5" fill="none" stroke="#fff"/></svg>
      <span>hello@orbitale.co</span>
    </div>
    <div class="contact-row" style="top:98px">
      <svg width="7" height="9" viewBox="0 0 8 11"><path d="M4 0a4 4 0 0 1 4 4c0 3-4 7-4 7S0 7 0 4a4 4 0 0 1 4-4z" fill="#fff"/><circle cx="4" cy="4" r="1.5" fill="#7fd9c1"/></svg>
      <span>Orbitale, Inc.<br>418 Larkmoor Ave. Fresno, CA 93710</span>
    </div>
  </div>
  <h2 class="callback-title heading">Request For Call Back</h2>
  <div class="field" style="left:322px;top:83px">Name</div>
  <div class="field" style="left:501px;top:83px">Email</div>
  <div class="field" style="left:322px;top:118px">Ph Num</div>
  <div class="field strong" style="left:501px;top:118px">Enquiry About</div>
  <div class="btn-outline" style="left:323px;top:157px;width:69px;height:25px;border-width:1.5px">Submit Now</div>
</section>

<footer class="footer">
  <p class="copyright">Copyright © 2018.<br>All rights reserved.</p>
  <nav class="foot-nav"><span class="active">Home</span><span>About Us</span><span>Service</span><span>Pricing</span><span>Contact Us</span><span>Account</span></nav>
  <div class="social">
    <i style="background:var(--social-1)"></i><i style="background:var(--social-2)"></i><i style="background:var(--social-3)"></i><i style="background:var(--social-4)"></i>
  </div>
</footer>

</body>
</html>
```